Business Card for a Jewellery Brand

Business card for an upscale jewellery brand. Attached is the brand logo and icon and color board. I am looking for two card versions: one for the founder and one is generic. The card should be elegant and convey upscale and premium feel. I am open to both square and rectangle card shapes.

Industry/Entity Type

Jewelry

Contact Information for Business Card

Two cards: (1) Sunela Parvaniya (Founder) (2) General
(1) Sunela Parvaniya card should have Name: Sunela Parvaniya, Title: Founder Email id: sunela@quiremo.com.au. Phone no: +61452913307
(2) Generic card should have Email id: info@quiremo.com.au. Phone no: +61436207518

Requirements
Must have
• Workmark
• ICON
• Phone no
• Email ID
• ABN: 58219740312 (Note: ABN is Business number in Australia)
• Website: www.quiremo.com.au
• Instagram: quiremo_jewellery
• Facebook: @quiremojewellery
Nice to have
• Tagline

```html
<!DOCTYPE html>
<html lang="en">
<head>
<meta charset="utf-8">
<title>Quiremo Jewellery – Business Card</title>
<link href="https://fonts.googleapis.com/css2?family=Open+Sans:wght@300;400;600&display=swap" rel="stylesheet">
<style>
  :root {
    --backdrop: #3b3330;
    --card: #0d0d0d;
    --rose: #e8958a;
    --ink: #f2f2f2;
    --silver: #cfcfcf;
    --divider: rgba(232,149,138,0.55);
  }
  * { box-sizing: border-box; margin: 0; padding: 0; }
  html, body { width: 1200px; height: 900px; overflow: hidden; }
  body {
    background: var(--backdrop);
    font-family: "Open Sans", Arial, sans-serif;
    position: relative;
  }
  .card {
    position: absolute;
    top: 292px;
    width: 520px;
    height: 316px;
    background: var(--card);
    border-radius: 3px;
    box-shadow: 0 10px 28px rgba(0,0,0,0.45);
  }
  .card--front { left: 50px; }
  .card--back  { left: 630px; display: flex; align-items: center; justify-content: center; }

  /* front */
  .front__brand {
    position: absolute;
    left: 40px; top: 112px;
    width: 170px;
    display: flex; align-items: center; gap: 10px;
    color: var(--rose);
    font-weight: 400;
    font-size: 22px;
    letter-spacing: 5px;
  }
  .front__brand-dot {
    width: 12px; height: 12px; border-radius: 50%;
    background: var(--rose); flex: none;
  }
  .front__divider {
    position: absolute;
    left: 232px; top: 48px;
    width: 1px; height: 130px;
    background: var(--divider);
  }
  .contact {
    position: absolute;
    left: 256px; top: 46px;
    color: var(--ink);
    font-size: 13px;
    line-height: 1.35;
  }
  .contact__name {
    color: var(--rose);
    font-size: 17px;
    font-weight: 600;
    letter-spacing: 0.8px;
    text-transform: uppercase;
  }
  .contact__title { font-size: 13px; }
  .contact__abn { margin-top: 2px; }
  .contact__abn-label { color: var(--rose); }
  .contact__list { list-style: none; margin-top: 14px; }
  .contact__item { display: flex; align-items: center; gap: 8px; font-size: 12.5px; line-height: 1.6; }
  .contact__icon { width: 10px; height: 10px; flex: none; fill: var(--rose); }

  .social {
    position: absolute;
    display: flex; align-items: center; gap: 8px;
    color: var(--ink);
    font-size: 13.5px;
  }
  .social--facebook { left: 40px; bottom: 30px; }
  .social--instagram { left: 256px; bottom: 86px; }
  .social__mark {
    width: 22px; height: 22px; border-radius: 50%;
    background: var(--rose); flex: none;
  }

  /* back */
  .back__wordmark {
    color: var(--silver);
    font-weight: 300;
    font-size: 40px;
    letter-spacing: 14px;
    padding-left: 14px;
  }
</style>
</head>
<body>
  <section class="card card--front" aria-label="Business card front">
    <div class="front__brand"><span class="front__brand-dot"></span>QUIREMO</div>
    <div class="front__divider"></div>

    <div class="contact">
      <p class="contact__name">Sunela Parvaniya</p>
      <p class="contact__title">Founder</p>
      <p class="contact__abn"><span class="contact__abn-label">ABN:</span> 58219740312</p>
      <ul class="contact__list">
        <li class="contact__item">
          <svg class="contact__icon" viewBox="0 0 10 10"><path d="M2 0.5 L3.6 2.6 L2.8 3.6 Q4 6 6.4 7.2 L7.4 6.4 L9.5 8 L8.4 9.5 Q4 9.4 0.5 1.6 Z"/></svg>
          +61452913307
        </li>
        <li class="contact__item">
          <svg class="contact__icon" viewBox="0 0 10 10"><path d="M0 2 H10 V8.5 H0 Z M0.6 2.4 L5 5.6 L9.4 2.4" stroke="#0d0d0d" stroke-width="0.8"/></svg>
          sunela@quiremo.com.au
        </li>
        <li class="contact__item">
          <svg class="contact__icon" viewBox="0 0 10 10"><circle cx="5" cy="5" r="4.6"/><path d="M0.6 5 H9.4 M5 0.5 Q2.6 5 5 9.5 M5 0.5 Q7.4 5 5 9.5" stroke="#0d0d0d" stroke-width="0.7" fill="none"/></svg>
          www.quiremo.com.au
        </li>
      </ul>
    </div>

    <div class="social social--instagram"><span class="social__mark"></span>quiremo_jewellery</div>
    <div class="social social--facebook"><span class="social__mark"></span>@quiremojewellery</div>
  </section>

  <section class="card card--back" aria-label="Business card back">
    <p class="back__wordmark">QUIREMO</p>
  </section>
</body>
</html>
```